BOLD & MINIMALIST DESIGN NEEDED

We want a very bold but minimalistic business card design that is impactful and utilizes both sides of the business card. Our current logo is included for your use.

We want bold fonts and good use of negative space. We don't want the logo to overpower the design.

Target Market(s)

Professionals who are building new commercial buildings.

Industry/Entity Type

Construction

Contact Information for Business Card

Name, Title, email, office phone, cell phone, website

Font styles to use
Serif
Sans Serif

Requirements
Must have
• Bold design!

```html
<!DOCTYPE html>
<html lang="en">
<head>
<meta charset="utf-8">
<title>Stonegate Design + Build — Business Card</title>
<link href="https://fonts.googleapis.com/css2?family=Fira+Sans:wght@400;500;800&display=swap" rel="stylesheet">
<style>
  :root {
    --green: #86c229;
    --ink: #0c0c0d;
    --paper: #ffffff;
    --backdrop: #e4e5e3;
    --text: #2a2a2a;
  }
  * { box-sizing: border-box; margin: 0; padding: 0; }
  html, body {
    width: 1200px; height: 1122px; overflow: hidden;
    background: var(--backdrop);
    font-family: "Fira Sans", Arial, sans-serif;
  }
  .canvas { position: relative; width: 1200px; height: 1122px; }

  .card {
    position: absolute; left: 220px;
    width: 760px; height: 434px;
    border-radius: 26px;
    overflow: hidden;
    box-shadow: 0 10px 30px rgba(0,0,0,.18);
  }

  /* Front side */
  .card-front { top: 80px; background: var(--green); }
  .brand {
    position: absolute; left: 50%; top: 50%;
    transform: translate(-50%, -50%);
    display: flex; flex-direction: column; align-items: center;
    color: var(--ink);
  }
  .brand-row { display: flex; align-items: center; gap: 18px; }
  .brand-square { width: 44px; height: 44px; background: var(--ink); }
  .brand-name {
    font-weight: 800; font-size: 64px; letter-spacing: 1px; line-height: 1;
  }
  .brand-rule { width: 100%; height: 2px; background: var(--ink); margin-top: 12px; }
  .brand-tagline {
    font-weight: 800; font-size: 20px; letter-spacing: 12px; margin-top: 8px;
  }

  /* Back side */
  .card-back { top: 568px; background: var(--paper); }
  .contact { position: absolute; left: 64px; top: 118px; color: var(--text); }
  .person-name {
    color: var(--green); font-weight: 800; font-size: 34px; letter-spacing: 1px; line-height: 1;
  }
  .person-title { font-size: 17px; margin-top: 6px; color: var(--ink); }
  .divider { width: 44px; height: 1.5px; background: var(--ink); margin: 14px 0 16px; }
  .contact-list { list-style: none; }
  .contact-list li {
    display: flex; align-items: center; gap: 12px;
    font-size: 17px; line-height: 1; margin-bottom: 11px;
  }
  .contact-list svg { width: 15px; height: 15px; flex: none; }

  .mark-block {
    position: absolute; right: 70px; bottom: 60px;
    width: 250px; height: 250px; background: var(--green);
  }
</style>
</head>
<body>
<main class="canvas">

  <section class="card card-front" aria-label="Card front">
    <div class="brand">
      <div class="brand-row">
        <span class="brand-square"></span>
        <span class="brand-name">STONEGATE</span>
      </div>
      <div class="brand-rule"></div>
      <div class="brand-tagline">DESIGN + BUILD</div>
    </div>
  </section>

  <section class="card card-back" aria-label="Card back">
    <div class="contact">
      <h1 class="person-name">DANIEL REYES</h1>
      <p class="person-title">Founder &amp; CEO</p>
      <div class="divider"></div>
      <ul class="contact-list">
        <li>
          <svg viewBox="0 0 24 24" fill="var(--green)"><path d="M6.6 10.8a15.2 15.2 0 0 0 6.6 6.6l2.2-2.2c.3-.3.7-.4 1-.2 1.1.4 2.3.6 3.6.6.6 0 1 .4 1 1V20c0 .6-.4 1-1 1A17 17 0 0 1 3 4c0-.6.4-1 1-1h3.5c.6 0 1 .4 1 1 0 1.3.2 2.5.6 3.6.1.3 0 .7-.2 1z"/></svg>
          (123) 456-7890
        </li>
        <li>
          <svg viewBox="0 0 24 24" fill="none" stroke="var(--green)" stroke-width="2.4"><rect x="6" y="2" width="12" height="20" rx="2"/><line x1="11" y1="18" x2="13" y2="18"/></svg>
          (123) 456-7890
        </li>
        <li>
          <svg viewBox="0 0 24 24" fill="var(--green)"><path d="M2 5h20v14H2z"/><path d="M2 5l10 8 10-8" fill="none" stroke="#fff" stroke-width="1.8"/></svg>
          info@stonegatebuild.com
        </li>
        <li>
          <svg viewBox="0 0 24 24" fill="none" stroke="var(--green)" stroke-width="2.2"><circle cx="12" cy="12" r="9.5"/><path d="M2.5 12h19M12 2.5c3 3 3 16 0 19M12 2.5c-3 3-3 16 0 19"/></svg>
          stonegatebuild.com
        </li>
      </ul>
    </div>
    <div class="mark-block"></div>
  </section>

</main>
</body>
</html>
```